School Website

I need a design for a School (2 sections: Primary 6-12 years and Secondary 12-18 years). The first page is just a choice of the 2 sections. After we'll need 2 websites (with the same structure: Menu, ...) but with different colors. In fact, we need for end of October, 6 design of school website. So the best websites are going to be made available to you in the future (in pixelharbor) but privately.

Target Market(s)

Public, Parents, ...

Coding

Coded - Design and coding required

Number of Pages Required

5+ page

Font styles to use
Sans Serif

Colors
34a6d7
85cae6
cee9f5
ffffff

Requirements
Must have
• You can check the old Website: http: / /velmot.be We need the same pages with the same content. Menu: - HomePage - News and communication (like blog page) - Activities (like blog page, with photo gallery) - Contact (Contact form + maps) - In the main menu, we need a special button to connect to an external Website ( button needs to be different than the other menu items The name of this button is "Parents Area"). The logo of 2 sections are attached. Please use it for the design and the choice of colors.
Nice to have
• This is a web design of other school that we like: https://www.quintelo.be

```html
<!DOCTYPE html>
<html lang="fr">
<head>
<meta charset="utf-8">
<title>Lycée Royal de Velmont – Section secondaire</title>
<link href="https://fonts.googleapis.com/css2?family=Open+Sans:wght@400;600;700&family=Bree+Serif&family=Raleway:wght@500;600&display=swap" rel="stylesheet">
<style>
:root{
  --orange:#f7941d;
  --orange-dark:#e8820a;
  --ink:#222;
  --text:#333;
  --muted:#777;
  --sky-top:#8fd0f2;
  --sky-bottom:#d9effa;
  --panel:#efefef;
  --mint:#d6f3e7;
  --dark:#3f4152;
  --map-land:#eceef0;
  --map-water:#c4e2f5;
  --white:#fff;
}
*{margin:0;padding:0;box-sizing:border-box}
html,body{width:1200px;height:3522px;overflow:hidden}
body{position:relative;font-family:"Open Sans",sans-serif;color:var(--text);
  background:linear-gradient(180deg,var(--sky-top) 0,#bfe4f7 300px,var(--sky-bottom) 1200px,#cfe9f7 100%)}
.abs{position:absolute}
.brand{left:85px;top:25px;display:flex;align-items:center;gap:10px}
.brand-dot{width:48px;height:48px;border-radius:50%;background:#1d5fa8}
.brand-name{font-family:"Open Sans",sans-serif;font-weight:700;font-size:22px;color:#1d5fa8}
.nav{left:85px;top:122px;width:799px;height:53px;background:linear-gradient(#fff,#f1f1f1);
  display:flex;align-items:center;font-family:"Raleway",sans-serif;font-size:15px;font-weight:600;color:#222}
.nav span{margin-left:24px}
.nav .sep{color:#444;margin-left:0;padding:0 50px}
.parents{left:898px;top:122px;width:216px;height:53px;border-radius:27px;background:var(--orange);
  color:#fff;font-family:"Raleway",sans-serif;font-size:16px;font-weight:600;display:flex;align-items:center}
.parents .ico{width:53px;height:53px;border-radius:50%;background:var(--orange-dark);display:flex;align-items:center;justify-content:center;margin-right:17px}
.page{left:85px;top:191px;width:1029px;height:2574px;background:var(--white)}
.hero{left:98px;top:204px;width:1005px;height:416px;background:linear-gradient(135deg,#6c8c5a,#b6c9a3 40%,#5d7290 70%,#35455c)}
.hero-title{position:absolute;left:22px;top:318px;font-family:"Bree Serif",serif;color:var(--orange);font-size:38px;line-height:1}
.hero-sub{position:absolute;left:22px;top:364px;font-family:"Bree Serif",serif;color:var(--orange);font-size:24px}
.arrow{position:absolute;top:194px;width:30px;height:30px;border-radius:50%;background:rgba(255,255,255,.25)}
.info{top:652px;display:flex;align-items:center;gap:12px;font-size:15px;line-height:23px;color:#222}
.vsep{top:650px;width:2px;height:62px;border-left:1px dashed #bbb}
.rule{left:85px;top:742px;width:1029px;height:4px;background:var(--orange)}
.h2{font-family:"Bree Serif",serif;font-size:25px;color:var(--ink);text-transform:uppercase}
.h2-line{height:1px;background:#ccc}
.card{width:302px}
.card .img{height:201px}
.card h3{font-size:16px;font-weight:600;color:#666;margin-top:13px}
.card p{font-size:12.5px;color:#888;line-height:21px;margin-top:6px}
.card .meta{display:flex;justify-content:space-between;margin-top:13px;font-size:11px}
.card .meta b{color:var(--orange);font-weight:600}
.card .meta i{font-style:normal;color:#555;font-size:10px}
.panel{top:1225px;width:470px;height:564px;background:linear-gradient(135deg,#e6e6e6,#f6f6f6 50%,#e8e8e8)}
.panel .pico{position:absolute;top:30px;left:50%;margin-left:-30px;width:60px;height:60px}
.panel h3{position:absolute;top:108px;width:100%;text-align:center;font-family:"Bree Serif",serif;font-size:22px;color:var(--ink)}
.panel .line{position:absolute;top:146px;left:75px;width:320px;height:1px;background:#bbb}
.panel .body{position:absolute;top:162px;font-size:15.5px;line-height:26px;color:#222}
.btn{display:inline-block;height:31px;line-height:31px;border-radius:16px;background:var(--orange);color:#fff;font-size:11px;font-weight:700;text-align:center;width:137px}
.conges{left:115px;top:1820px;width:970px;height:334px;background:linear-gradient(90deg,var(--mint),#e4f6ee)}
.conges h3{position:absolute;left:24px;top:30px;font-family:"Bree Serif",serif;font-size:22px;color:var(--ink)}
.conges .body{position:absolute;left:26px;top:70px;font-size:15.5px;line-height:26px;color:#222}
.thumb{width:249px;height:186px}
.thumb .img{height:147px}
.thumb .bar{height:39px;background:var(--orange);color:#fff;font-size:13px;font-weight:700;display:flex;align-items:center;justify-content:space-between;padding:0 12px}
.thumb .go{width:22px;height:22px;border-radius:50%;background:#fff;display:flex;align-items:center;justify-content:center}
.doc{font-size:16px;line-height:40px;color:var(--orange)}
.doc-lead{font-size:16px;color:#222;border-left:4px solid var(--orange);padding-left:14px}
.pdf{display:inline-block;width:20px;height:25px;border:2px solid var(--orange);border-radius:2px;vertical-align:middle;margin-left:8px}
.contact{left:85px;top:2765px;width:1029px;height:428px;background:var(--dark);color:#fff}
.contact h3{position:absolute;left:32px;top:40px;font-family:"Bree Serif",serif;font-size:22px}
.contact .lead{position:absolute;left:32px;top:103px;font-size:13.5px;line-height:24px}
.contact .row{position:absolute;left:32px;display:flex;align-items:center;gap:12px;font-size:15px}
.field label{display:block;font-size:13.5px;margin-bottom:7px}
.field div{background:#fff;border:1px solid #ddd}
.send{position:absolute;left:500px;top:315px;width:170px;height:38px;background:var(--orange);font-size:13.5px;display:flex;align-items:center;justify-content:center}
.map{left:85px;top:3193px;width:1029px;height:274px;background:linear-gradient(90deg,var(--map-land) 0,#e4eaef 45%,var(--map-water) 60%,#e4eaef 75%,var(--map-land) 100%)}
.footer{left:0;top:3467px;width:1200px;height:55px;background:var(--orange);color:#fff;font-size:14px}
.social{position:absolute;top:14px;width:28px;height:28px;border-radius:50%}
</style>
</head>
<body>

<div class="abs brand"><span class="brand-dot"></span><span class="brand-name">Lycée Royal de Velmont</span></div>

<nav class="abs nav">
  <span>HOME</span><span class="sep">|</span><span style="margin-left:0">NEWS &amp; COMMUNICATION</span><span class="sep">|</span><span style="margin-left:0">ACTIVITIES</span><span class="sep">|</span><span style="margin-left:0">CONTACT</span>
</nav>
<div class="abs parents"><span class="ico"><svg width="28" height="20" viewBox="0 0 28 20"><circle cx="10" cy="6" r="5" fill="#fff"/><circle cx="20" cy="6" r="4" fill="#fff"/><path d="M0 20c0-6 5-8 10-8s10 2 10 8z" fill="#fff"/><path d="M18 12c5 0 10 2 10 8h-6c0-3-1-6-4-8z" fill="#fff"/></svg></span>PARENTS AREA</div>

<div class="abs page"></div>

<div class="abs hero" role="img" aria-label="Photo de groupe d'élèves du secondaire marchant en plein air">
  <span class="arrow" style="left:14px"></span><span class="arrow" style="right:14px"></span>
  <div class="hero-title">Lycée Royal de Velmont</div>
  <div class="hero-sub">Section secondaire</div>
</div>

<div class="abs info" style="left:183px">
  <svg width="32" height="38" viewBox="0 0 32 38"><path d="M16 2a11 11 0 0 0-11 11c0 8 11 19 11 19s11-11 11-19A11 11 0 0 0 16 2z" fill="var(--orange)"/><circle cx="16" cy="13" r="4" fill="#fff"/><ellipse cx="16" cy="35" rx="12" ry="2.5" fill="none" stroke="var(--orange)" stroke-width="1.5"/></svg>
  <div>Quai des Tilleuls,5, 4500 Velmont,<br>Belgique</div>
</div>
<div class="abs vsep" style="left:450px"></div>
<div class="abs info" style="left:502px">
  <svg width="38" height="38" viewBox="0 0 38 38"><circle cx="19" cy="19" r="16" fill="none" stroke="var(--orange)" stroke-width="3"/><path d="M19 9v10h8" fill="none" stroke="var(--orange)" stroke-width="3"/></svg>
  <div>Du lundi au vendredi<br>7h00 – 17h</div>
</div>
<div class="abs vsep" style="left:740px"></div>
<div class="abs info" style="left:775px">
  <svg width="38" height="38" viewBox="0 0 38 38"><path d="M8 4l6 8-4 4c2 5 6 9 11 11l4-4 8 6-4 6C16 34 4 22 3 9z" fill="var(--orange)"/><path d="M22 4a13 13 0 0 1 12 12M22 10a7 7 0 0 1 6 6" fill="none" stroke="var(--orange)" stroke-width="2.5"/></svg>
  <div>Appelez-nous Maintenant<br>+32 81 604 350</div>
</div>
<div class="abs rule"></div>

<div class="abs h2" style="left:0;width:1200px;text-align:center;top:784px">Nouvelles et communication</div>
<div class="abs h2-line" style="left:427px;top:827px;width:320px"></div>

<article class="abs card" style="left:112px;top:861px">
  <div class="img" role="img" aria-label="Photo d'un bâtiment scolaire vitré" style="background:linear-gradient(160deg,#3b6fb6,#9cc3ea 50%,#2a3340)"></div>
  <h3>TITLE HERE</h3>
  <p>Lorem ipsum dolor sit amet, consecteturing elit, sed do eiusmod tempor incidi dunt ut labore et</p>
  <div class="meta"><b>READ MORE</b><i>06, SEP - 2016</i></div>
</article>
<article class="abs card" style="left:451px;top:861px">
  <div class="img" role="img" aria-label="Photo de mains réunies en cercle" style="background:linear-gradient(135deg,#8aa7c4,#d4a58a 50%,#4c5f7a)"></div>
  <h3>TITLE HERE</h3>
  <p>Lorem ipsum dolor sit amet, consecteturing elit, sed do eiusmod tempor incidi dunt ut labore et</p>
  <div class="meta"><b>READ MORE</b><i>06, SEP - 2016</i></div>
</article>
<article class="abs card" style="left:782px;top:861px">
  <div class="img" role="img" aria-label="Photo de visiteurs dans une salle d'exposition" style="background:linear-gradient(180deg,#d9dcdf,#8f9499 60%,#c9cccf)"></div>
  <h3>TITLE HERE</h3>
  <p>Lorem ipsum dolor sit amet, consecteturing elit, sed do eiusmod tempor incidi dunt ut labore et</p>
  <div class="meta"><b>READ MORE</b><i>06, SEP - 2016</i></div>
</article>

<section class="abs panel" style="left:115px">
  <div class="pico" role="img" aria-label="Icône équipe" style="background:linear-gradient(#f6b26b,#d9534f);border-radius:8px"></div>
  <h3>NOTRE ÉQUIPE PÉDAGOGIQUE</h3>
  <div class="line"></div>
  <div class="body" style="left:20px">
    <b>Direction:</b><br>Madame la Préfète des Etudes, Claire Dumont<br>Madame le Proviseur, Martine Lefèvre<br>
    <b>Accueil:</b><br>Madame Sophie Renard :<br>081/604350<br>Fax général : 081/604126<br>
    <b>Secrétaire de Direction:</b><br>Madame Delcourt Laura:<br>081/604353<br>Economat:<br>Monsieur Julien Marchal:<br>081/604356
  </div>
  <span class="btn abs" style="left:20px;top:500px">VIEW MORE</span>
</section>

<section class="abs panel" style="left:614px">
  <div class="pico" role="img" aria-label="Icône calendrier et horloge" style="background:linear-gradient(#7fb3d5,#e74c3c);border-radius:8px"></div>
  <h3>NOS HORAIRES ET GARDERIES</h3>
  <div class="line"></div>
  <div class="body" style="left:23px;width:430px">
    Les horaires de cours sont définis comme suit :<br>Tous les jours de 8h25 à 15h25.&nbsp; Sauf le mercredi:<br>de 8h25 à 12h20.<br>Une garderie est organisée dès 7h00 dans les bâtiments de la section primaire.<br>Dès la fin des cours, les enfants sont encadrés par les titulaires puis pris en charge en garderie dès 15h35 et au plus tard jusque 18h00.<br>Le mercredi, de 12h30 à 18h00, différentes activités sont proposées en fonction de la météo.<br><br>Les garderies du soir et du mercredi sont payantes.
  </div>
  <span class="btn abs" style="left:23px;top:500px">VIEW MORE</span>
</section>

<section class="abs conges">
  <h3>CONGÉS SCOLAIRES</h3>
  <div class="body">
    L'établissement sera ouvert jusqu'au 5 juillet 2018 inclus et à partir du 16 août<br>2018 de 9h à 15h.<br>Rentrée scolaire : lundi 3 septembre<br>Fête de la Communauté française : jeudi 27 septembre<br>Congé d'automne (Toussaint) : Du lundi 29 octobre au vendredi 2 novembre 2018<br>Vacances d'hiver (Noël) : Du lundi 24 décembre 2018 au vendredi 4 janvier 2019<br>Congé de détente (Carnaval) : Du lundi 4 mars 2019 au vendredi 8 mars 2019
  </div>
  <span class="btn abs" style="left:26px;top:268px">VIEW MORE</span>
  <div class="abs" role="img" aria-label="Illustration d'un panneau en bois « vacances » avec bouée et ballon de plage" style="left:725px;top:30px;width:220px;height:255px;border-radius:12px;background:linear-gradient(180deg,#c9833f 0,#b46e2c 45%,#e8f4f0 60%,#e04b3c 85%,#3fa7d6)"></div>
</section>

<div class="abs" role="img" aria-label="Icône montagnes" style="left:115px;top:2195px;width:70px;height:70px;background:linear-gradient(135deg,#8ed0f0,#f3c03c 50%,#4caf50)"></div>
<div class="abs h2" style="left:203px;top:2215px;font-size:23px;text-transform:none">ACTIVITÉS</div>

<div class="abs thumb" style="left:113px;top:2296px"><div class="img" role="img" aria-label="Photo d'élèves en sortie en forêt" style="background:linear-gradient(160deg,#6a6f5c,#c9b8b3 55%,#3d3f45)"></div><div class="bar">AUGUST 04, 2016<span class="go"><svg width="8" height="10"><path d="M1 1l5 4-5 4" fill="none" stroke="var(--orange)" stroke-width="2"/></svg></span></div></div>
<div class="abs thumb" style="left:387px;top:2296px"><div class="img" role="img" aria-label="Photo d'élèves en activité en classe" style="background:linear-gradient(160deg,#7b5a2e,#e0b98a 55%,#4a3a2a)"></div><div class="bar">AUGUST 04, 2016<span class="go"><svg width="8" height="10"><path d="M1 1l5 4-5 4" fill="none" stroke="var(--orange)" stroke-width="2"/></svg></span></div></div>
<div class="abs thumb" style="left:113px;top:2511px"><div class="img" role="img" aria-label="Photo d'élèves lors d'un atelier" style="background:linear-gradient(160deg,#9aa0a5,#3c6f9c 55%,#2b2e33)"></div><div class="bar">AUGUST 04, 2016<span class="go"><svg width="8" height="10"><path d="M1 1l5 4-5 4" fill="none" stroke="var(--orange)" stroke-width="2"/></svg></span></div></div>
<div class="abs thumb" style="left:387px;top:2511px"><div class="img" role="img" aria-label="Photo d'un groupe d'élèves en visite" style="background:linear-gradient(160deg,#3c4a6a,#b8a27a 55%,#2f3240)"></div><div class="bar">AUGUST 04, 2016<span class="go"><svg width="8" height="10"><path d="M1 1l5 4-5 4" fill="none" stroke="var(--orange)" stroke-width="2"/></svg></span></div></div>

<div class="abs" role="img" aria-label="Icône presse-papiers" style="left:715px;top:2192px;width:72px;height:72px;border-radius:50%;background:linear-gradient(135deg,#e74c6f,#3d5a9e)"></div>
<div class="abs h2" style="left:802px;top:2215px;font-size:23px;text-transform:none">RÈGLEMENT INTÉRIEUR</div>
<div class="abs" style="left:715px;top:2290px">
  <div class="doc-lead">Veuillez trouvez ci-joint le règlement intérieur:<br><span class="doc" style="line-height:34px">règlement intérieur<span class="pdf"></span></span></div>
  <div class="doc-lead" style="margin-top:36px;line-height:48px;border-left-width:4px">Veuillez trouvez ci-joint les grilles horaires:</div>
  <div class="doc" style="padding-left:16px">
    Grille d'option 1ère année<span class="pdf"></span><br>
    Grille d'option 2ème année<span class="pdf"></span><br>
    Grille d'option 3ème année<span class="pdf"></span><br>
    Grille d'option 4ème année<span class="pdf"></span><br>
    Grille d'option 5ème année<span class="pdf"></span><br>
    Grille d'option 6ème année<span class="pdf"></span>
  </div>
</div>

<section class="abs contact">
  <h3>CONTACTEZ-NOUS</h3>
  <div class="abs" style="left:32px;top:84px;width:100px;height:1px;background:#9a9ba6"></div>
  <p class="lead">If you have any questions or comments about our services<br>please fill out this form. We would love to hear from you.</p>
  <div class="row" style="top:172px"><svg width="22" height="24" viewBox="0 0 22 24"><path d="M11 1a8 8 0 0 0-8 8c0 6 8 14 8 14s8-8 8-14a8 8 0 0 0-8-8z" fill="none" stroke="#fff" stroke-width="2"/><circle cx="11" cy="9" r="3" fill="#fff"/></svg>Quai des Tilleuls,5, 4500 Velmont, Belgique</div>
  <div class="row" style="top:214px"><svg width="22" height="22" viewBox="0 0 22 22"><circle cx="11" cy="11" r="9" fill="none" stroke="#fff" stroke-width="2"/><path d="M11 5v6h5" fill="none" stroke="#fff" stroke-width="2"/></svg>Du lundi au vendredi - 7h00 -17h</div>
  <div class="row" style="top:256px"><svg width="22" height="22" viewBox="0 0 22 22"><path d="M4 2l4 5-2 3c1 3 3 5 6 6l3-2 5 4-3 3C9 21 1 13 1 5z" fill="none" stroke="#fff" stroke-width="2"/></svg>Appelez-nous Maintenant:&nbsp; +32 81 604 350</div>
  <div class="abs" style="left:32px;top:308px;width:92px;height:90px;background:#fff"></div>
  <div class="abs field" style="left:500px;top:38px;width:240px"><label>Full Name*</label><div style="height:43px"></div></div>
  <div class="abs field" style="left:761px;top:38px;width:240px"><label>Email *</label><div style="height:43px"></div></div>
  <div class="abs field" style="left:500px;top:128px;width:501px"><label>Message*</label><div style="height:143px"></div></div>
  <div class="send">SEND MESSAGE</div>
</section>

<div class="abs map" role="img" aria-label="Carte de localisation de l'établissement au bord de la rivière"></div>

<footer class="abs footer">
  <span class="abs" style="left:117px;top:17px">© Copyright 2019 velmot.be</span>
  <span class="social" style="left:983px;background:#3b5bb5"></span>
  <span class="social" style="left:1020px;background:#3aa0e0"></span>
  <span class="social" style="left:1057px;background:#d93f8e"></span>
</footer>

</body>
</html>
```